Kellwyn Surface Records

I have a current web site that it looking quite aged and it needs a new lease of life. This is a Graffiti Management Website so is all about data processing and management of information. I want a html 5 view on any platform design. clean crisp and new. I have provided some screen shots of my current site.

Target Market(s)

The Target Market will be local government. most users will not be heavy pc users

Industry/Entity Type

Management

Font styles to use
Sans Serif
Other font styles liked:
• web font like calibri

Colors

Designer to choose colors to be used in the design.

Requirements
Must have
• Must have menus similar to attachments

```html
<!DOCTYPE html>
<html lang="en">
<head>
<meta charset="utf-8">
<title>Kellwyn Surface Records</title>
<link href="https://fonts.googleapis.com/css2?family=Open+Sans:wght@300;400;600;700&display=swap" rel="stylesheet">
<style>
:root{
  --teal:#2aa3a6;
  --teal-dark:#1f7f82;
  --ink:#333a3d;
  --muted:#8a9094;
  --band-dark:#555758;
  --footer:#47494a;
  --header:rgba(34,44,48,.82);
  --white:#ffffff;
  --light:#e9eced;
  --pie-dark:#4a4c4e;
  --pie-grey:#b3b5b6;
}
*{box-sizing:border-box;margin:0;padding:0}
html,body{width:1200px;height:3512px;overflow:hidden}
body{font-family:"Open Sans",Arial,sans-serif;color:var(--ink);background:var(--white);position:relative}
.section{position:absolute;left:0;width:1200px}

/* hero */
.hero{top:0;height:732px}
.hero-art{position:absolute;inset:0;background:linear-gradient(120deg,#3e5a5c 0%,#6a4d6e 30%,#8a5a3c 55%,#3c6a6a 80%,#2e3e44 100%)}
.hero-shade{position:absolute;inset:0;background:rgba(30,36,40,.45)}
.site-header{position:absolute;top:0;left:0;width:1200px;height:132px;background:var(--header)}
.brand{position:absolute;left:84px;top:26px;color:var(--white)}
.brand-name{font-size:40px;font-weight:400;letter-spacing:14px;line-height:1}
.brand-tag{margin-top:10px;font-size:15px;color:var(--teal);border-top:1px solid var(--teal);padding-top:4px;letter-spacing:1px;text-transform:uppercase;width:260px}
.main-nav{position:absolute;left:456px;top:42px;display:flex;gap:0}
.main-nav a{color:var(--white);font-size:15px;font-weight:600;text-decoration:none;text-transform:uppercase;padding:0 22px}
.main-nav a.active{color:var(--teal);border-bottom:2px solid var(--teal);padding-bottom:6px}
.sub-nav{position:absolute;right:88px;top:92px;display:flex;font-size:14px;font-weight:600;color:var(--white)}
.sub-nav span{padding:0 16px}
.sub-nav span+span{border-left:1px solid rgba(255,255,255,.5)}
.hero-title{position:absolute;top:200px;width:100%;text-align:center;color:var(--white);font-size:44px;font-weight:300;line-height:58px;letter-spacing:1px}
.hero-title::after{content:"";display:block;width:560px;height:2px;margin:14px auto 0;background:rgba(255,255,255,.6)}
.feature-label-top{position:absolute;left:80px;top:446px;color:var(--white);font-size:14px;font-weight:700}
.features{position:absolute;top:474px;left:0;width:1200px;height:200px}
.feature{position:absolute;width:200px;margin-left:-100px;text-align:center;color:var(--white);font-size:14px;text-transform:uppercase}
.feature svg{display:block;margin:0 auto 10px}
.dash{position:absolute;height:4px;width:40px;background:var(--white)}

/* help band */
.help{top:732px;height:161px;background:var(--teal);color:var(--white)}
.help-kicker{position:absolute;left:88px;top:32px;font-size:17px;font-weight:600;text-transform:uppercase}
.help-phone{position:absolute;left:88px;top:62px;display:flex;align-items:center;gap:14px;font-size:52px;font-weight:600}
.help-note{position:absolute;left:500px;top:56px;width:240px;text-align:center;font-size:17px;font-weight:600;line-height:22px;text-transform:uppercase}
.help-rule{position:absolute;left:762px;top:36px;width:1px;height:90px;background:rgba(255,255,255,.5)}
.btn-register{position:absolute;left:825px;top:52px;width:316px;height:64px;background:#26494b;color:var(--white);font-size:18px;font-weight:600;text-transform:uppercase;display:flex;align-items:center;justify-content:center}

/* headings */
.section-title{position:absolute;width:100%;text-align:center;color:var(--teal);font-size:36px;font-weight:400;text-transform:uppercase;letter-spacing:1px}
.section-title::after{content:"";display:block;width:330px;height:1px;margin:6px auto 0;background:var(--teal)}

/* about */
.about{top:893px;height:571px}
.about .section-title{top:20px}
.about-points{position:absolute;left:132px;top:100px;width:1010px;display:grid;grid-template-columns:453px 453px;column-gap:104px;row-gap:14px;font-size:14px;line-height:19px;color:var(--ink)}
.about-points p{position:relative;padding-left:26px}
.about-points p::before{content:"";position:absolute;left:0;top:6px;border-left:8px solid var(--teal);border-top:4px solid transparent;border-bottom:4px solid transparent}
.about-points p.wide{grid-column:1 / span 2;width:420px;margin-left:498px}
.brand-word{color:var(--teal)}
.about-rule{position:absolute;left:585px;top:306px;width:30px;height:3px;background:var(--muted)}
.team{position:absolute;left:138px;top:330px;width:930px;display:flex;justify-content:space-between}
.member{width:140px;text-align:center}
.member .portrait{width:130px;height:130px;margin:0 auto;border-radius:50%;background:radial-gradient(circle at 50% 40%,#d8c8b8 0%,#9b8d82 60%,#6d6a68 100%)}
.member .name{margin-top:12px;font-size:11px;color:var(--muted);text-transform:uppercase;line-height:15px}
.member .line{width:30px;height:2px;background:var(--light);margin:10px auto 0}

/* report */
.report{top:1464px;height:541px;border-top:1px solid var(--light)}
.report .section-title{top:36px}
.report-intro{position:absolute;left:230px;top:100px;width:740px;text-align:center;font-size:14px;line-height:20px}
.stats{position:absolute;left:138px;top:200px;width:440px}
.stat{position:relative;height:62px}
.stat-label{font-size:12px;color:var(--ink)}
.stat-bar{position:absolute;left:0;top:24px;width:296px;height:5px;background:var(--light)}
.stat-fill{height:100%;background:var(--teal)}
.stat-value{position:absolute;left:324px;top:4px;font-size:28px;font-weight:300}
.stat-flag{position:absolute;left:402px;top:8px;width:6px;height:6px;border-radius:50%;background:#7cc47c}
.stat-flag.down{background:#d65a5a}
.pie{position:absolute;left:893px;top:146px}
.report-outro{position:absolute;left:200px;top:464px;width:800px;text-align:center;font-size:14px;line-height:20px}

/* benefits */
.benefits{top:2005px;height:497px;background:var(--band-dark);color:var(--white)}
.benefits .section-title{top:22px;color:var(--white)}
.benefits .section-title::after{background:rgba(255,255,255,.6)}
.benefit-grid{position:absolute;left:88px;top:86px;width:1024px;display:grid;grid-template-columns:repeat(4,256px)}
.benefit{text-align:center;padding:0 14px}
.benefit-badge{width:180px;height:180px;margin:0 auto;border-radius:50%;border:1px solid rgba(255,255,255,.12);display:flex;flex-direction:column;align-items:center;justify-content:center;gap:12px}
.benefit-name{font-size:15px;color:var(--teal);text-transform:uppercase}
.benefit-text{margin-top:60px;font-size:14px;line-height:19px;height:76px}
.read-more{display:inline-block;margin-top:20px;width:150px;height:42px;line-height:40px;border:1px solid var(--teal);color:var(--teal);font-size:14px}

/* legislation */
.legislation{top:2502px;height:396px}
.legislation .section-title{top:52px}
.law-grid{position:absolute;left:88px;top:126px;width:1024px;display:grid;grid-template-columns:497px 497px;column-gap:30px;row-gap:35px}
.law{height:88px;border:2px solid #bfe4e5;display:flex;align-items:center;justify-content:center;text-align:center;color:var(--teal);font-size:14px;text-transform:uppercase;padding:0 20px}

/* contacts */
.contacts{top:2898px;height:93px;background:var(--teal)}
.contacts .section-title{top:20px;color:var(--white)}
.contacts .section-title::after{background:rgba(255,255,255,.7)}
.map{position:absolute;left:0;top:2991px;width:1200px;height:229px;background:linear-gradient(135deg,#ece6d6 0%,#f3d9a0 35%,#e8e2d0 60%,#a9c8e8 100%)}

/* footer */
.site-footer{top:3220px;height:292px;background:var(--footer);color:var(--white)}
.foot-brand{position:absolute;left:84px;top:60px}
.foot-brand .brand-name{font-size:34px;letter-spacing:12px}
.foot-brand .brand-tag{color:var(--white);border-top-color:var(--white);width:220px;font-size:13px}
.copyright{position:absolute;left:84px;top:150px;font-size:12px;color:#cfd1d2}
.foot-col{position:absolute;top:62px;font-size:14px;line-height:20px}
.foot-col h3{font-size:17px;font-weight:600;text-transform:uppercase;margin-bottom:24px}
.foot-contact{left:520px;text-align:center;width:200px}
.foot-location{left:820px;width:260px;text-align:center}
.social{position:absolute;left:960px;top:220px;display:flex;gap:12px}
.social span{width:30px;height:30px;border-radius:50%;border:1px solid rgba(255,255,255,.6)}
</style>
</head>
<body>

<section class="section hero">
  <div class="hero-art" role="img" aria-label="Colourful graffiti-covered wall, blurred behind the header"></div>
  <div class="hero-shade"></div>
  <header class="site-header">
    <div class="brand">
      <div class="brand-name">KSR</div>
      <div class="brand-tag">Kellwyn Surface Records</div>
    </div>
    <nav class="main-nav">
      <a class="active">Home</a><a>Products</a><a>Reports</a><a>Benefits</a><a>Legislation</a><a>Contact us</a>
    </nav>
    <div class="sub-nav"><span>LOGIN</span><span>DEMO LOGIN</span></div>
  </header>
  <h1 class="hero-title">HELPING YOU CLEAN UP<br>YOUR COMMUNITY</h1>
  <div class="feature-label-top">GRAFFITI REGISTER</div>
  <div class="features">
    <div class="feature" style="left:181px;top:0">
      <svg width="116" height="116" viewBox="0 0 116 116"><circle cx="58" cy="58" r="58" fill="#fff"/><rect x="48" y="46" width="20" height="38" rx="4" fill="#333a3d"/><rect x="53" y="36" width="10" height="10" fill="#333a3d"/><circle cx="72" cy="36" r="2" fill="#333a3d"/><circle cx="78" cy="32" r="2" fill="#333a3d"/></svg>
    </div>
    <div class="feature" style="left:322px;top:8px">
      <svg width="100" height="100" viewBox="0 0 100 100"><circle cx="50" cy="50" r="50" fill="rgba(40,46,50,.75)"/><rect x="34" y="38" width="32" height="24" fill="none" stroke="#fff" stroke-width="2"/><path d="M36 60l10-10 8 7 5-4 6 7" fill="none" stroke="#fff" stroke-width="2"/></svg>
      Graffiti photos
    </div>
    <div class="feature" style="left:498px;top:8px">
      <svg width="100" height="100" viewBox="0 0 100 100"><circle cx="50" cy="50" r="50" fill="rgba(40,46,50,.75)"/><rect x="38" y="32" width="24" height="36" fill="none" stroke="#fff" stroke-width="2"/><rect x="46" y="40" width="8" height="18" fill="#fff"/></svg>
      Graffiti archive
    </div>
    <div class="feature" style="left:673px;top:8px">
      <svg width="100" height="100" viewBox="0 0 100 100"><circle cx="50" cy="50" r="50" fill="rgba(40,46,50,.75)"/><path d="M34 36h12l4 4h16v24H34z" fill="none" stroke="#fff" stroke-width="2"/><circle cx="54" cy="52" r="5" fill="none" stroke="#fff" stroke-width="2"/><path d="M58 56l6 6" stroke="#fff" stroke-width="2"/></svg>
      Searchable database
    </div>
    <div class="feature" style="left:878px;top:8px">
      <svg width="100" height="100" viewBox="0 0 100 100"><circle cx="50" cy="50" r="50" fill="rgba(40,46,50,.75)"/><path d="M34 34v32h32" fill="none" stroke="#fff" stroke-width="2"/><path d="M38 58l8-10 6 6 12-14" fill="none" stroke="#fff" stroke-width="2"/></svg>
      Statistical analysis<br>reports
    </div>
    <div class="feature" style="left:1054px;top:8px">
      <svg width="100" height="100" viewBox="0 0 100 100"><circle cx="50" cy="50" r="50" fill="rgba(40,46,50,.75)"/><path d="M36 44h22l-5-5M64 56H42l5 5" fill="none" stroke="#fff" stroke-width="2"/></svg>
      Data conversion
    </div>
  </div>
  <div class="dash" style="left:128px;top:665px"></div>
</section>

<section class="section help">
  <div class="help-kicker">Just in case you need any help:</div>
  <div class="help-phone">
    <svg width="40" height="48" viewBox="0 0 40 48"><path d="M10 2c4 0 6 10 4 12l-4 3c2 7 7 14 13 18l4-3c3-2 12 4 11 8-1 5-6 8-11 7C15 45 2 28 2 12 2 6 5 2 10 2z" fill="#fff"/></svg>
    (02) 9123 4876
  </div>
  <div class="help-note">Our expert staff is standing by to answer your questions</div>
  <div class="help-rule"></div>
  <div class="btn-register">Register now</div>
</section>

<section class="section about">
  <h2 class="section-title">About us</h2>
  <div class="about-points">
    <p><span class="brand-word">KSR</span> is an Online Database System to Manage Graffiti in your area or Your Properties</p>
    <p><span class="brand-word">KSR</span> allows you to Register, Track, Report and Archive Graffiti Jobs with Photographic Records</p>
    <p><span class="brand-word">KSR</span> allows sharing of Critical Graffiti Tag and Photographic Data between its subscribers, assisting with tracking down Serial Graffiti Offenders</p>
    <p><span class="brand-word">KSR</span> has a Statistical and Comparison Reporting System to allow its subscribers to graphically report and compare their Graffiti Data</p>
    <p class="wide"><span class="brand-word">KSR</span> records both Estimated and Actual hours and costs for each job enabling you to track the effectiveness of Anti Graffiti policy</p>
  </div>
  <div class="about-rule"></div>
  <div class="team">
    <div class="member"><div class="portrait" role="img" aria-label="Team member portrait"></div><div class="name">Lena Hart<br>(Manager)</div><div class="line"></div></div>
    <div class="member"><div class="portrait" role="img" aria-label="Team member portrait"></div><div class="name">Owen Price<br>(Support)</div><div class="line"></div></div>
    <div class="member"><div class="portrait" role="img" aria-label="Team member portrait"></div><div class="name">Mia Dalton<br>(Director)</div><div class="line"></div></div>
    <div class="member"><div class="portrait" role="img" aria-label="Team member portrait"></div><div class="name">Jake Moran<br>(Analyst)</div><div class="line"></div></div>
    <div class="member"><div class="portrait" role="img" aria-label="Team member portrait"></div><div class="name">Ruby Lane<br>(Developer)</div><div class="line"></div></div>
    <div class="member"><div class="portrait" role="img" aria-label="Team member portrait"></div><div class="name">Sam Fielder<br>(Designer)</div><div class="line"></div></div>
  </div>
</section>

<section class="section report">
  <h2 class="section-title">Report</h2>
  <p class="report-intro">Statistical Reports can be done instantaneously and can be run on any data stored with in <span class="brand-word">KSR</span>. Charts and Graphs are available to clearly show trends and details for Management Purposes.</p>
  <div class="stats">
    <div class="stat"><div class="stat-label">Graffiti type Report (10 -10-2014 to 10-12-2014)</div><div class="stat-bar"><div class="stat-fill" style="width:50.5%"></div></div><div class="stat-value">50,5%</div><div class="stat-flag"></div></div>
    <div class="stat"><div class="stat-label">Graffiti type Report (10 -10-2014 to 10-12-2014)</div><div class="stat-bar"><div class="stat-fill" style="width:20%"></div></div><div class="stat-value">20%</div><div class="stat-flag down"></div></div>
    <div class="stat"><div class="stat-label">Graffiti type Report (10 -10-2014 to 10-12-2014)</div><div class="stat-bar"><div class="stat-fill" style="width:29.5%"></div></div><div class="stat-value">29.5%</div><div class="stat-flag"></div></div>
  </div>
  <svg class="pie" width="292" height="292" viewBox="0 0 292 292" role="img" aria-label="Pie chart of graffiti types">
    <g transform="rotate(-90 146 146)" fill="none" stroke-width="146">
      <circle cx="146" cy="146" r="73" stroke="var(--pie-grey)" stroke-dasharray="91.73 366.94"/>
      <circle cx="146" cy="146" r="73" stroke="var(--teal)" stroke-dasharray="135.31 323.36" stroke-dashoffset="-91.73"/>
      <circle cx="146" cy="146" r="73" stroke="var(--pie-dark)" stroke-dasharray="231.63 227.04" stroke-dashoffset="-227.04"/>
    </g>
  </svg>
  <p class="report-outro">Comparison reports (both historically and geographically) can show the effectiveness of anti graffiti policy.<br>Detail Reports can be run Monthly, Quarterly and Annually</p>
</section>

<section class="section benefits">
  <h2 class="section-title">Benefits</h2>
  <div class="benefit-grid">
    <div class="benefit">
      <div class="benefit-badge"><svg width="44" height="32" viewBox="0 0 44 32"><rect x="4" y="6" width="36" height="20" fill="var(--teal)"/><circle cx="22" cy="16" r="5" fill="#555758"/></svg><div class="benefit-name">Cost effective</div></div>
      <p class="benefit-text"><span class="brand-word">KSR</span> allows you to track the cost and effectiveness of your Graffiti Removal. Compare the estimates...</p>
      <span class="read-more">Read more</span>
    </div>
    <div class="benefit">
      <div class="benefit-badge"><svg width="36" height="36" viewBox="0 0 36 36"><rect x="4" y="4" width="28" height="28" fill="none" stroke="var(--teal)" stroke-width="3"/><path d="M10 12h16M10 18h16M10 24h10" stroke="var(--teal)" stroke-width="3"/></svg><div class="benefit-name">Photographic records</div></div>
      <p class="benefit-text">Store any photographic records of New, Existing and Completed Graffiti Jobs. Archive all completed...</p>
      <span class="read-more">Read more</span>
    </div>
    <div class="benefit">
      <div class="benefit-badge"><svg width="40" height="36" viewBox="0 0 40 36"><circle cx="12" cy="6" r="4" fill="var(--teal)"/><circle cx="28" cy="6" r="4" fill="var(--teal)"/><rect x="8" y="12" width="8" height="22" fill="var(--teal)"/><rect x="24" y="12" width="8" height="22" fill="var(--teal)"/></svg><div class="benefit-name">Assist prosecution</div></div>
      <p class="benefit-text"><span class="brand-word">KSR</span> can assist with the possible prosecution of offenders with records of previous tags inside...</p>
      <span class="read-more">Read more</span>
    </div>
    <div class="benefit">
      <div class="benefit-badge"><svg width="30" height="36" viewBox="0 0 30 36"><path d="M8 16v-6a7 7 0 0 1 14 0v6" fill="none" stroke="var(--teal)" stroke-width="3"/><rect x="3" y="16" width="24" height="18" fill="var(--teal)"/></svg><div class="benefit-name">Access and security</div></div>
      <p class="benefit-text">You can access your data from any PC around the world connected to the Internet. You can give...</p>
      <span class="read-more">Read more</span>
    </div>
  </div>
</section>

<section class="section legislation">
  <h2 class="section-title">Legislation</h2>
  <div class="law-grid">
    <div class="law">NSW Graffiti Legislation</div>
    <div class="law">NSW Government perspective on graffiti</div>
    <div class="law">NSW Local Government Graffiti Ammendment Act 2002</div>
    <div class="law">NSW Local Government Legislation regarding graffiti removal</div>
  </div>
</section>

<section class="section contacts">
  <h2 class="section-title">Contacts</h2>
</section>
<div class="map" role="img" aria-label="Street map of the office area with a location marker"></div>

<footer class="section site-footer">
  <div class="foot-brand">
    <div class="brand-name">KSR</div>
    <div class="brand-tag">Kellwyn Surface Records</div>
  </div>
  <div class="copyright">copyright 2014 KSR all rights reserved</div>
  <div class="foot-col foot-contact">
    <h3>Contact us</h3>
    <p>Tell Phone: (02) 9123 4876</p>
    <p style="margin-top:10px">enquiries@kellwynsr.com.au<br>support@kellwynsr.com.au</p>
  </div>
  <div class="foot-col foot-location">
    <h3>Location</h3>
    <p>Kellwyn Surface Records<br>PO Box 318, Brindlemere, NSW 2290</p>
  </div>
  <div class="social"><span></span><span></span><span></span><span></span></div>
</footer>

</body>
</html>
```